Business Card For Halvenmoor Financial Consulting

Hi, I would like a business card designed. Bold, modern.
Please use the same design as the logo. I have also attached the website design to see the overall theme.
Wordmark Font
Color: Hex: #01AEF7

```html
<!DOCTYPE html>
<html lang="en">
<head>
<meta charset="utf-8">
<title>Halvenmoor Financial Consulting – Business Card</title>
<link rel="stylesheet" href="https://fonts.googleapis.com/css2?family=Montserrat:wght@400;600;700&display=swap">
<style>
  :root {
    --backdrop: #8c8c8c;
    --card-blue: #3ca8e0;
    --brand-blue: #01aef7;
    --ink-navy: #14202b;
    --white: #ffffff;
  }
  * { box-sizing: border-box; margin: 0; padding: 0; }
  html, body {
    width: 1160px; height: 1200px; overflow: hidden;
    background: var(--backdrop);
    font-family: "Montserrat", Arial, sans-serif;
    color: var(--white);
  }
  .card {
    position: absolute; left: 199px; width: 777px; height: 442px;
    background: var(--card-blue);
  }
  .card--front { top: 104px; }
  .card--back { top: 634px; }

  .brand-block {
    position: absolute; background: var(--ink-navy);
    display: flex; align-items: center;
  }
  .brand-mark {
    flex: none; border: 3px solid var(--brand-blue);
  }
  .brand-name {
    font-weight: 600; color: var(--white); line-height: 1.1;
  }
  .brand-name span { display: block; }

  .card--front .brand-block {
    left: 31px; top: 37px; width: 308px; height: 71px;
    padding: 0 14px 0 10px; gap: 12px;
  }
  .card--front .brand-mark { width: 44px; height: 44px; }
  .card--front .brand-name .word { font-size: 27px; letter-spacing: 1px; }
  .card--front .brand-name .tag { font-size: 9.5px; letter-spacing: 2.6px; margin-top: 3px; }

  .card--back .brand-block {
    left: 118px; top: 159px; width: 542px; height: 126px;
    padding: 0 22px 0 18px; gap: 22px;
  }
  .card--back .brand-mark { width: 80px; height: 80px; border-width: 4px; }
  .card--back .brand-name .word { font-size: 48px; letter-spacing: 2px; }
  .card--back .brand-name .tag { font-size: 16px; letter-spacing: 5px; margin-top: 6px; }

  .holder {
    position: absolute; right: 32px; top: 48px; text-align: right;
  }
  .holder-name { font-size: 31px; font-weight: 700; letter-spacing: 0.2px; line-height: 1.1; }
  .holder-title { font-size: 20px; font-weight: 400; margin-top: 4px; }

  .contact-list {
    position: absolute; left: 31px; top: 312px; list-style: none;
  }
  .contact-list li {
    display: flex; align-items: center; gap: 8px;
    height: 37px; font-size: 19.5px;
  }
  .contact-icon { width: 24px; height: 24px; flex: none; }

  .address {
    position: absolute; right: 33px; top: 357px;
    text-align: right; font-size: 19.5px; line-height: 28px; font-style: normal;
  }
</style>
</head>
<body>
  <section class="card card--front" aria-label="Card front">
    <div class="brand-block">
      <div class="brand-mark"></div>
      <div class="brand-name">
        <span class="word">HALVENMOOR</span>
        <span class="tag">FINANCIAL CONSULTING</span>
      </div>
    </div>

    <div class="holder">
      <p class="holder-name">DALIA RENWICK</p>
      <p class="holder-title">Senior Consultant</p>
    </div>

    <ul class="contact-list">
      <li>
        <svg class="contact-icon" viewBox="0 0 24 24" aria-hidden="true">
          <circle cx="12" cy="12" r="12" fill="#14202b"/>
          <path d="M5 10c0-2 3-3 7-3s7 1 7 3v1h-3v-1.5h-8V11H5z" fill="#fff"/>
          <rect x="7.5" y="11" width="9" height="6" rx="1" fill="#fff"/>
        </svg>
        <span>+1 555 014 2290</span>
      </li>
      <li>
        <svg class="contact-icon" viewBox="0 0 24 24" aria-hidden="true">
          <circle cx="12" cy="12" r="12" fill="#14202b"/>
          <rect x="5.5" y="7.5" width="13" height="9" fill="#fff"/>
          <path d="M5.5 7.5l6.5 5 6.5-5" fill="none" stroke="#14202b" stroke-width="1.3"/>
        </svg>
        <span>info@halvenmoor.com</span>
      </li>
      <li>
        <svg class="contact-icon" viewBox="0 0 24 24" aria-hidden="true">
          <circle cx="12" cy="12" r="12" fill="#14202b"/>
          <circle cx="12" cy="12" r="7" fill="none" stroke="#fff" stroke-width="1.5"/>
          <path d="M5 12h14M12 5c-3 3.5-3 10.5 0 14M12 5c3 3.5 3 10.5 0 14" fill="none" stroke="#fff" stroke-width="1.2"/>
        </svg>
        <span>www.halvenmoor.com</span>
      </li>
    </ul>

    <address class="address">
      42-07 Larkspur Ave 12<br>
      Brookfield, NY 11420
    </address>
  </section>

  <section class="card card--back" aria-label="Card back">
    <div class="brand-block">
      <div class="brand-mark"></div>
      <div class="brand-name">
        <span class="word">HALVENMOOR</span>
        <span class="tag">FINANCIAL CONSULTING</span>
      </div>
    </div>
  </section>
</body>
</html>
```